Economics of an Assumption vs Obtaining a New Loan at Current Market Rate

I need to marketing flyer that has fields that calculate mortgage payments amongst other calculations. I have a rough draft that I will attach.

The idea is to provide a tool for a real estate agent to use to illustrate to a potential buyer what a payment would be if they assumed the existing loan on the house or took out a new loan at current market.

The flyer needs to be able to allow an agent to drop in their logo, photo, and contact along with the loan officers photo and contact info.

You can google open house flyer to see examples of what the overall artwork and presentation can look like.

Target Market(s)

Home Buyers

Industry/Entity Type

Real Estate

Colors
F0912C
F2A743
F7CA91
FBE8D2
FDF5EE
EE7325
F08F49
F5BC92
FAE3D3
FDF4ED

Requirements
Must have
• A way to calculate mortgage payment
Nice to have
• Photo and logo drop ins

```html
<!DOCTYPE html>
<html lang="en">
<head>
<meta charset="utf-8">
<title>Open House Flyer – Assumption vs New Loan</title>
<link rel="stylesheet" href="https://fonts.googleapis.com/css2?family=Poppins:wght@300;400;500;600;800;900&family=Oswald:wght@500;600&display=swap">
<style>
:root{
  --orange:#EE7325;
  --orange-dark:#B9520F;
  --brown:#7A3A10;
  --ink:#2B2B2B;
  --panel:#3A3A3A;
  --band:#353535;
  --paper:#FFFFFF;
  --stage:#ECEEF2;
  --veil:rgba(255,255,255,.78);
}
*{margin:0;padding:0;box-sizing:border-box}
html,body{width:691px;height:1200px;overflow:hidden;background:var(--stage);font-family:'Poppins',sans-serif;color:var(--ink)}
.flyer{position:absolute;left:0;top:153px;width:691px;height:894px;background:var(--paper);overflow:hidden;box-shadow:0 6px 18px rgba(0,0,0,.18)}
.abs{position:absolute}
.hero-photo{left:0;top:0;width:691px;height:397px;background:linear-gradient(180deg,#6FA0D8 0%,#A9C7E6 30%,#9C5A44 48%,#B8B8B0 62%,#5F8A36 82%,#4C7A2A 100%)}
.hero-veil{left:0;top:32px;width:380px;height:305px;background:var(--veil)}
.hero-veil .logo-zone{position:absolute;left:0;top:0;width:380px;height:130px;background:rgba(255,255,255,.55)}
.brand{left:48px;top:58px;display:flex;align-items:center;gap:12px}
.brand .mark{width:26px;height:26px;background:var(--orange)}
.brand .name{font-size:40px;font-weight:400;color:var(--ink);line-height:1}
.invite{left:36px;top:176px;font-size:20px;font-weight:500;letter-spacing:.2px;color:var(--ink)}
.headline{left:34px;top:196px;font-weight:900;line-height:.86;font-size:74px;letter-spacing:-1px}
.headline .open{display:block;color:var(--ink)}
.headline .house{display:block;color:var(--brown)}
.price-band{left:0;top:337px;width:389px;height:60px;background:var(--orange)}
.price-band .label{position:absolute;left:34px;top:15px;color:#fff;font-size:21px;font-weight:600}
.price-band .field{position:absolute;left:245px;top:16px;width:129px;height:26px;background:#fff}
.calc{width:289px;height:217px}
.calc .head{position:absolute;left:0;top:0;width:289px;height:30px}
.calc .head span{position:absolute;left:0;right:0;top:3px;text-align:center;font-family:'Oswald',sans-serif;font-weight:600;color:#fff;font-size:16px;letter-spacing:-.2px}
.calc .body{position:absolute;left:0;top:30px;width:289px;height:187px;background:var(--panel)}
.row-label{position:absolute;left:12px;color:#fff;font-size:12.5px;line-height:1.1}
.box{position:absolute;background:#fff;font-size:12px;color:var(--ink);padding:0 12px;height:17px;line-height:17px;white-space:nowrap}
.box.tall{height:37px;line-height:14px;padding-top:4px}
.total{position:absolute;left:12px;top:175px;width:260px;height:24px;display:flex}
.total .tag{width:139px;border:1px solid var(--orange);color:var(--orange);font-size:17px;padding-left:9px;line-height:22px;background:var(--panel)}
.total .sum{flex:1;background:#fff}
.lbl{font-size:13px;color:var(--ink)}
.inp{border:1px solid #555;height:24px;line-height:22px;font-size:12px;padding-left:9px;background:#fff}
.tag-orange{background:var(--orange);color:#fff;font-size:10px;line-height:10px;padding:2px 9px;height:24px}
.ribbon{left:128px;top:757px;width:434px;height:24px}
.ribbon span{position:absolute;left:0;right:0;top:2px;text-align:center;color:#fff;font-weight:600;font-size:15px}
.drop-band{left:0;top:765px;width:691px;height:129px;background:var(--band)}
.drop{position:absolute;top:36px;display:flex;align-items:flex-start;gap:10px}
.drop .caption{color:var(--orange);font-size:13.5px;line-height:16px;text-align:right;padding-top:3px}
.drop .caption i{display:block;font-style:normal;letter-spacing:1px;color:#fff;font-size:10px;line-height:8px}
.drop .slot{width:71px;height:63px;background:#fff;border-bottom:3px solid var(--band);box-shadow:0 2px 0 #fff}
</style>
</head>
<body>
<main class="flyer">
  <div class="abs hero-photo" role="img" aria-label="Photo of the listed property: two-storey brick house with white porches, lawn and trees"></div>
  <div class="abs hero-veil"><div class="logo-zone"></div></div>
  <div class="abs brand"><span class="mark"></span><span class="name">Nestora</span></div>
  <p class="abs invite">COME JOIN US AT OUR</p>
  <h1 class="abs headline" style="top:200px"><span class="open">OPEN</span><span class="house">HOUSE</span></h1>
  <div class="abs price-band"><span class="label">PURCHASE PRICE :</span><span class="field"></span></div>

  <section class="abs calc" style="left:36px;top:409px">
    <svg class="head" viewBox="0 0 289 30" aria-hidden="true">
      <polygon points="0,30 14,0 275,0 289,30" fill="var(--orange)"/>
      <polygon points="0,30 14,0 10,30" fill="var(--orange-dark)"/>
      <polygon points="289,30 275,0 279,30" fill="var(--orange-dark)"/>
    </svg>
    <div class="head"><span>CURRENT MORTGAGE</span></div>
    <div class="body"></div>
    <span class="row-label" style="top:51px">Loan amount:</span><span class="box" style="left:152px;top:51px;width:120px">Allow input</span>
    <span class="row-label" style="top:80px">Interest rate :</span><span class="box" style="left:152px;top:80px;width:120px">Allow input</span>
    <span class="row-label" style="top:109px">Principal &amp; Interest:</span><span class="box" style="left:152px;top:109px;width:120px">Allow input</span>
    <span class="row-label" style="top:137px">Mortgage Insurance:</span><span class="box" style="left:152px;top:137px;width:120px">Allow input</span>
    <div class="total"><span class="tag">TOTAL</span><span class="sum"></span></div>
  </section>

  <section class="abs calc" style="left:367px;top:409px">
    <svg class="head" viewBox="0 0 289 30" aria-hidden="true">
      <polygon points="0,30 14,0 275,0 289,30" fill="var(--orange)"/>
      <polygon points="0,30 14,0 10,30" fill="var(--orange-dark)"/>
      <polygon points="289,30 275,0 279,30" fill="var(--orange-dark)"/>
    </svg>
    <div class="head"><span>NEW MORTGAGE 10%. DOWN PAYMENT</span></div>
    <div class="body"></div>
    <span class="row-label" style="top:51px">Loan amount:</span><span class="box" style="left:128px;top:51px;width:147px;padding:0 6px">10% of purchase price</span>
    <span class="row-label" style="top:80px">Market rate:</span><span class="box" style="left:154px;top:80px;width:121px">Input</span>
    <span class="row-label" style="top:109px">Principal Interest:</span><span class="box" style="left:154px;top:109px;width:121px">Input%</span>
    <span class="row-label" style="top:133px">Mortgage<br>insurace:</span><span class="box tall" style="left:103px;top:131px;width:172px">Principal Interest+<br>Montgage &amp; +insusance</span>
    <div class="total"><span class="tag">TOTAL</span><span class="sum"></span></div>
  </section>

  <span class="abs lbl" style="left:36px;top:647px">Years</span>
  <span class="abs inp" style="left:78px;top:644px;width:55px">Input</span>
  <span class="abs lbl" style="left:154px;top:647px">Months</span>
  <span class="abs inp" style="left:212px;top:644px;width:55px">Input</span>
  <span class="abs tag-orange" style="left:267px;top:644px;width:58px">Left on<br>loan</span>
  <span class="abs lbl" style="left:367px;top:646px">Term</span>
  <span class="abs inp" style="left:408px;top:643px;width:200px">Input</span>
  <span class="abs lbl" style="left:616px;top:646px">years</span>

  <span class="abs lbl" style="left:36px;top:684px">Telta</span>
  <span class="abs inp" style="left:78px;top:681px;width:248px">Purchase price minus loan amount</span>
  <span class="abs lbl" style="left:367px;top:684px">DOWN Payment Amount</span>
  <span class="abs inp" style="left:535px;top:681px;width:119px"></span>

  <span class="abs lbl" style="left:147px;top:722px">Payment difference</span>
  <span class="abs inp" style="left:282px;top:719px;width:247px">Difference Between Totals</span>

  <div class="abs drop-band" role="img" aria-label="Dark band with a faint house photo behind the drop-in spaces">
    <div class="drop" style="left:36px"><span class="caption">DROP<br>PHOTO<i>••••••</i></span><span class="slot"></span></div>
    <div class="drop" style="left:194px"><span class="caption">DROP<br>CONTACT<br>INFO<i>••••••</i></span><span class="slot"></span></div>
    <div class="drop" style="left:373px"><span class="caption">DROP<br>PHOTO<i>••••••</i></span><span class="slot"></span></div>
    <div class="drop" style="left:532px"><span class="caption">DROP<br>LOGO<i>••••••</i></span><span class="slot"></span></div>
  </div>

  <div class="abs ribbon">
    <svg width="434" height="24" viewBox="0 0 434 24" aria-hidden="true" style="position:absolute;left:0;top:0">
      <polygon points="0,0 434,0 420,24 14,24" fill="var(--orange)"/>
    </svg>
    <span>THIS PROPERTY IS "TAKE MY LOW RATE CERTIFIED"</span>
  </div>
</main>
</body>
</html>
```